WordPress Design for both website and landing page for an expert

I need a clean and stylish design for my new website. I work as an expert (see attached file WHY HOW WHAT), my product is expert opinion (reports) for company evaluations You can use all of the attached pictures colored or black / white. The person is me, you can add other pictures, if you want. The design should be clean and stylish, so you could use white, black, gray, silver and / or one additional color. I have added an idea about my website, see attached file CONCEPT WEBSITE If you have any more information, please do not hesitate to contact us 'Hesitate to ask me ...

```html
<!DOCTYPE html>
<html lang="en">
<head>
<meta charset="utf-8">
<title>Lukas Verhoven – Expert for Company Valuations</title>
<link href="https://fonts.googleapis.com/css2?family=Raleway:ital,wght@0,300;0,400;0,500;0,600;0,700;1,400&display=swap" rel="stylesheet">
<style>
:root{
  --black:#000000;
  --ink:#222428;
  --white:#ffffff;
  --blue:#3653c4;
  --blue-dark:#2b45ab;
  --grey:#8b8e93;
  --grey-light:#e3e5e8;
  --silver:#b9bdc2;
}
*{box-sizing:border-box;margin:0;padding:0}
html,body{width:1200px;height:2497px;overflow:hidden}
body{position:relative;font-family:"Raleway",sans-serif;color:var(--ink);background:var(--white)}
.abs{position:absolute}

/* header */
.site-header{position:absolute;left:0;top:0;width:1200px;height:110px;background:var(--black)}
.brand{position:absolute;left:112px;top:38px;width:210px;text-align:center;color:var(--white);font-size:20px;font-weight:400;letter-spacing:5px;white-space:nowrap}
.nav{position:absolute;top:38px;left:462px;display:flex;align-items:center;height:34px}
.nav a{color:var(--white);text-decoration:none;font-size:14px;font-weight:600;margin-right:24px;padding:0 0;line-height:34px;white-space:nowrap}
.nav a.active{background:var(--blue);padding:0 20px;margin-right:20px}
.nav .search{margin-right:28px;margin-left:4px}
.lang{width:60px;height:30px;border:1px solid #555;color:var(--white);font-size:11px;font-weight:600;display:flex;align-items:center;justify-content:center;gap:6px}

/* hero */
.hero{position:absolute;left:0;top:110px;width:1200px;height:616px;background:linear-gradient(90deg,#7d8186 0%,#a2a6aa 45%,#74777b 70%,#4f5256 100%)}
.hero h1{position:absolute;left:110px;top:220px;color:var(--white);font-weight:400;font-size:50px;line-height:70px;letter-spacing:0.5px}
.hero p{position:absolute;left:112px;top:374px;color:var(--white);font-size:19px;font-weight:500}
.btn{display:flex;align-items:center;justify-content:space-between;background:var(--blue);color:var(--white);font-weight:700;border-radius:30px;text-transform:uppercase}
.hero .btn{position:absolute;left:112px;top:434px;width:143px;height:47px;padding:0 7px 0 20px;font-size:13px}
.arrow-dot{width:34px;height:34px;border-radius:50%;background:var(--white);display:flex;align-items:center;justify-content:center}
.dots{position:absolute;left:562px;top:562px;display:flex;gap:7px}
.dots span{width:9px;height:9px;border-radius:50%;background:var(--white)}
.dots span.on{background:var(--blue)}

/* reasons */
.reasons{position:absolute;left:0;top:726px;width:1200px;height:622px;background:linear-gradient(160deg,#ffffff 0%,#f3f4f6 55%,#dfe2e6 100%)}
.mark-small{position:absolute;left:0;width:1200px;text-align:center;font-size:16px;font-weight:600;letter-spacing:3px}
.eyebrow{position:absolute;top:128px;width:1200px;text-align:center;color:var(--blue);font-size:16px;font-weight:500}
.reasons h2{position:absolute;top:166px;width:1200px;text-align:center;font-size:24px;font-weight:400;color:var(--ink)}
.card{position:absolute;top:274px;width:268px;height:241px;background:var(--white);box-shadow:0 2px 10px rgba(0,0,0,.14);text-align:center;padding-top:30px}
.card svg{display:block;margin:0 auto}
.card h3{margin-top:22px;font-size:16px;font-weight:700;color:var(--ink)}
.card p{margin:12px auto 0;width:230px;font-size:11.5px;line-height:25px;color:var(--grey)}
.card.featured{background:var(--blue)}
.card.featured h3,.card.featured p{color:var(--white)}

/* faq */
.faq{position:absolute;left:0;top:1348px;width:1200px;height:644px;background:linear-gradient(120deg,#5c5e61 0%,#83868a 45%,#4b4d50 100%)}
.faq h2{position:absolute;top:128px;width:1200px;text-align:center;color:var(--white);font-size:36px;font-weight:400}
.faq-item{position:absolute;left:163px;width:874px;height:50px;background:var(--white);box-shadow:0 2px 6px rgba(0,0,0,.25);display:flex;align-items:center;justify-content:space-between;padding:0 20px;font-size:14px;font-weight:500;color:var(--ink)}
.faq-item b{color:var(--blue);font-weight:600}
.faq-item.open{background:var(--blue);color:var(--white)}
.faq-item.open b{color:var(--white)}
.plus{width:13px;height:13px;border-radius:50%;background:#777;color:var(--white);font-size:11px;line-height:13px;text-align:center;font-weight:700}
.faq-item.open .plus{background:var(--white);color:var(--blue)}
.faq .claim{position:absolute;top:495px;width:1200px;text-align:center;color:var(--white);font-size:19px;font-weight:600}
.faq .note{position:absolute;top:534px;width:1200px;text-align:center;color:var(--white);font-size:12px;font-style:italic}
.faq .note u{margin-right:6px}

/* promise */
.promise{position:absolute;left:112px;top:2048px;width:976px;height:155px;border:1px solid #d5d7da}
.promise h2{position:absolute;left:37px;top:30px;color:var(--blue);font-size:25px;font-weight:400}
.promise p{position:absolute;left:40px;top:76px;width:460px;font-size:13px;line-height:25px;color:var(--grey)}
.promise .mark-mid{position:absolute;left:520px;top:56px;width:170px;text-align:center;font-size:22px;font-weight:700;color:#8b9097;letter-spacing:2px}
.promise .btn{position:absolute;left:730px;top:46px;width:205px;height:60px;padding:0 10px 0 26px;font-size:16px;font-weight:600}

/* footer */
.site-footer{position:absolute;left:0;top:2266px;width:1200px;height:231px;background:var(--black)}
.footer-mark{position:absolute;left:170px;top:100px;width:280px;text-align:center;color:var(--silver);font-size:26px;font-weight:700;letter-spacing:3px}
.footer-divider{position:absolute;left:488px;top:48px;width:1px;height:134px;background:#333}
.socials{position:absolute;left:554px;top:50px;display:flex;gap:5px}
.socials span{width:40px;height:40px;border-radius:50%;border:2px solid var(--white)}
.footer-nav{position:absolute;left:555px;top:124px;color:var(--white);font-size:13px;font-weight:500;word-spacing:2px}
.footer-nav i{font-style:normal;margin:0 12px}
.copyright{position:absolute;left:557px;top:162px;color:var(--white);font-size:12px}
</style>
</head>
<body>

<header class="site-header">
  <div class="brand">LUKAS VERHOVEN</div>
  <nav class="nav">
    <a class="active">HOME</a>
    <a>WHAT I DO</a>
    <a>WHY I DO IT &amp; HOW I DO IT</a>
    <a>ABOUT ME</a>
    <a class="search"><svg width="14" height="14" viewBox="0 0 14 14"><circle cx="6" cy="6" r="4.2" fill="none" stroke="#3653c4" stroke-width="2"/><line x1="9" y1="9" x2="13" y2="13" stroke="#3653c4" stroke-width="2"/></svg></a>
    <div class="lang">ENG <svg width="7" height="4" viewBox="0 0 7 4"><path d="M0 0h7L3.5 4z" fill="#fff"/></svg></div>
  </nav>
</header>

<section class="hero" role="img" aria-label="Portrait photo of the valuation expert in a suit standing in a bright office hallway">
  <h1>EXPERT FOR<br>COMPANY VALUATIONS</h1>
  <p>You need an opinion to determine the value of your company</p>
  <div class="btn">Read more <span class="arrow-dot"><svg width="14" height="14" viewBox="0 0 14 14"><circle cx="7" cy="7" r="6.5" fill="#3653c4"/><path d="M4 7h5M7 4.5 9.5 7 7 9.5" stroke="#fff" stroke-width="1.6" fill="none"/></svg></span></div>
  <div class="dots"><span></span><span></span><span class="on"></span><span></span><span></span></div>
</section>

<section class="reasons" role="img" aria-label="Faint background photo of financial documents and a pen">
  <div class="mark-small" style="top:84px;color:#8b9097">LV</div>
  <div class="eyebrow">WHY CHOOSE US</div>
  <h2>3 REASONS, WHY YOU SHOULD WORK WITH ME</h2>

  <article class="card" style="left:153px">
    <svg width="52" height="52" viewBox="0 0 52 52" fill="none" stroke="#3653c4" stroke-width="2"><circle cx="28" cy="30" r="17"/><path d="M24 8h8M28 8v5M28 30l7-8M41 15l3-3"/><path d="M4 26h7M2 32h9M5 38h7" stroke-width="1.5"/></svg>
    <h3>FAST</h3>
    <p>You will receive your report promptly (within a maximum of 21 days after receipt of all required documents)</p>
  </article>

  <article class="card featured" style="left:466px">
    <svg width="52" height="52" viewBox="0 0 52 52" fill="none" stroke="#fff" stroke-width="2"><path d="M8 6h30v40H8z"/><path d="M4 6h4M14 14h18M14 20h18M14 26h10"/><circle cx="34" cy="34" r="7"/><path d="M30 40l-2 8 6-3 6 3-2-8"/></svg>
    <h3>CERTIFIED</h3>
    <p>You receive a qualified and reliable report from a certified expert (highest acceptance by all parties)</p>
  </article>

  <article class="card" style="left:777px">
    <svg width="56" height="52" viewBox="0 0 56 52" fill="none" stroke="#3653c4" stroke-width="2"><path d="M16 50V38c-6-4-8-10-7-17C11 10 19 4 29 4c10 0 17 7 17 16l5 9h-5v9h-8v12"/><path d="M2 14h52M20 14v14M30 8v18M40 14v10"/><circle cx="20" cy="30" r="2"/><circle cx="30" cy="28" r="2"/><circle cx="40" cy="26" r="2"/></svg>
    <h3>UNDERSTANDABLE</h3>
    <p>Your report will be logical and comprehensible for you and will not contain any "technical Chinese"</p>
  </article>
</section>

<section class="faq" role="img" aria-label="Background photo of hands writing notes beside a laptop">
  <div class="mark-small" style="top:94px;color:#fff">LV</div>
  <h2>FAQ'S</h2>
  <div class="faq-item open" style="top:210px"><span><b>Q .</b> What are the buying motives of the customers?</span><span class="plus">+</span></div>
  <div class="faq-item" style="top:271px"><span><b>Q .</b> You want to sell shares of your company or your entire company?</span><span class="plus">+</span></div>
  <div class="faq-item" style="top:334px"><span><b>Q .</b> You want to transfer your business to your heirs and need a valuation for the tax office?</span><span class="plus">+</span></div>
  <div class="faq-item" style="top:397px"><span><b>Q .</b> You have to pay someone in the context of a separation / divorce and need a tax base?</span><span class="plus">+</span></div>
  <div class="claim">Have your company evaluated by a qualified expert and avoid many (unnecessary) quarrels.</div>
  <div class="note"><u>Note</u>: The cost of a report are always disproportionately cheaper than the cost of legal disputes. And that detached from the psychological burden of such an argument</div>
</section>

<section class="promise">
  <h2>MY QUALITY PROMISE</h2>
  <p>should the advised date for the preparation of the report be exceeded, you will receive the report free of charge</p>
  <div class="mark-mid">LV</div>
  <div class="btn">I waive my fee <span class="arrow-dot" style="width:38px;height:38px"><svg width="16" height="16" viewBox="0 0 14 14"><circle cx="7" cy="7" r="6.5" fill="#3653c4"/><path d="M4 7h5M7 4.5 9.5 7 7 9.5" stroke="#fff" stroke-width="1.6" fill="none"/></svg></span></div>
</section>

<footer class="site-footer">
  <div class="footer-mark">LUKAS VERHOVEN</div>
  <div class="footer-divider"></div>
  <div class="socials" aria-label="Social media links">
    <span></span><span></span><span></span><span></span><span></span><span></span>
  </div>
  <div class="footer-nav">HOME<i>/</i>WHAT I DO<i>/</i>WHY I DO IT &amp; HOW I DO IT<i>/</i>ABOUT ME</div>
  <div class="copyright">© Copyright 2018 Companyname All Rights Reserved</div>
</footer>

</body>
</html>
```